menu board design: rustle burger

we are a burger restaurant.
we need to re design our menu board to fit within the new design of the restaurant. we are after something simple and easy to read. the overall look and feel of the design should be inline with the design of the shop.

Target Market(s)

18-40 male and female

Colors

Designer to choose colors to be used in the design.

Requirements
Must have
• easy to read. good layout. white background. branding included in design.

```html
<!DOCTYPE html>
<html lang="en">
<head>
<meta charset="utf-8">
<title>Rustle Burger Menu Board</title>
<link href="https://fonts.googleapis.com/css2?family=Luckiest+Guy&family=Amatic+SC:wght@700&family=Open+Sans:wght@400;600;700&family=Permanent+Marker&family=Bungee&family=Hind:wght@500;600;700&display=swap" rel="stylesheet">
<style>
:root{
  --ink:#2e2e2e;
  --note:#363636;
  --blue:#1f58a6;
  --blue-dark:#17457f;
  --blue-shadow:#1b2a44;
  --red:#e2284b;
  --white:#ffffff;
  --paper:#ffffff;
}
*{box-sizing:border-box;margin:0;padding:0}
html,body{width:1200px;height:600px;overflow:hidden;background:var(--paper)}
.board{position:relative;width:1200px;height:600px;font-family:"Open Sans",sans-serif;color:var(--ink)}

.menu-panel{position:absolute;border:3px dashed var(--ink);border-radius:22px}
.panel-beef{left:22px;top:26px;width:358px;height:554px}
.panel-chicken{left:416px;top:166px;width:352px;height:414px}

.section-title{position:absolute;z-index:2;white-space:nowrap;overflow:hidden;font-family:"Luckiest Guy",sans-serif;font-weight:400;font-size:20px;letter-spacing:0;color:var(--white);-webkit-text-stroke:1.5px var(--ink);paint-order:stroke fill;text-shadow:2px 2px 0 var(--ink);line-height:26px;height:28px}
.title-beef{left:46px;top:76px;width:180px}
.title-chicken{left:448px;top:190px;width:198px;font-size:18.5px}

.note{position:absolute;z-index:1;background:var(--note);color:var(--white);border-radius:16px;font-weight:700;font-size:8.4px;line-height:1.1;text-align:center;text-transform:uppercase;display:flex;align-items:center;justify-content:center;padding:4px 9px}
.note-beef{left:238px;top:38px;width:128px;height:90px}
.note-chicken{left:658px;top:172px;width:102px;height:84px;padding:4px 6px}

.double-tag{position:absolute;font-family:"Amatic SC",sans-serif;font-weight:700;font-size:19px;letter-spacing:1px;background:var(--white);border:1px solid #bbb;box-shadow:2px 3px 3px rgba(0,0,0,.3);text-align:center;line-height:22px;height:24px;white-space:nowrap}

.item-name{position:absolute;font-weight:600;font-size:19px;letter-spacing:1.2px;line-height:1;text-transform:uppercase;white-space:nowrap}
.item-price{position:absolute;font-weight:600;font-size:19px;line-height:1}
.item-desc{position:absolute;font-size:9.4px;line-height:1.08;text-transform:uppercase;width:200px}

.brand{position:absolute;left:480px;top:30px;width:240px;text-align:center;font-family:"Open Sans",sans-serif;font-weight:700;font-size:36px;color:var(--blue);line-height:1.05}
.tagline{position:absolute;left:480px;top:148px;width:240px;text-align:center;font-size:9px;letter-spacing:2.4px;color:var(--blue-dark)}

.sides-title{position:absolute;left:880px;top:14px;width:232px;text-align:center;font-family:"Permanent Marker",cursive;font-weight:400;font-size:46px;letter-spacing:4px;color:var(--blue);line-height:1.1;white-space:nowrap}
.sides-panel{position:absolute;left:816px;top:80px;width:358px;height:500px;background:var(--blue);border-radius:20px;color:var(--white);font-family:"Hind",sans-serif}
.sides-panel .row{position:absolute;font-weight:500;font-size:19px;line-height:1;white-space:nowrap}
.sides-panel .small{position:absolute;font-weight:700;font-size:11.5px;line-height:1.05;text-transform:uppercase}
.sides-panel .mid{position:absolute;font-weight:700;font-size:13px;line-height:1.15;white-space:nowrap}

.sub-title{position:absolute;left:0;width:358px;text-align:center;white-space:nowrap;font-family:"Luckiest Guy",sans-serif;font-weight:400;font-size:21px;letter-spacing:.5px;color:var(--white);-webkit-text-stroke:1.5px var(--blue-shadow);paint-order:stroke fill;text-shadow:2px 2px 0 var(--blue-shadow);line-height:1}
.choose{position:absolute;left:0;width:358px;text-align:center;font-family:"Bungee",sans-serif;font-weight:400;font-size:12px;color:var(--red);line-height:1;white-space:nowrap}
.red{color:var(--red)}

.sauce-pill{position:absolute;left:164px;top:426px;width:92px;height:32px;border:1px dashed var(--white);border-radius:16px;font-family:"Bungee",sans-serif;font-weight:400;font-size:7px;color:var(--red);text-align:center;line-height:1.2;display:flex;align-items:center;justify-content:center;white-space:nowrap}
.callout{position:absolute;left:266px;top:410px;width:80px;height:84px;background:var(--white);color:var(--ink);border-radius:8px;font-size:6.6px;font-weight:700;line-height:1.12;text-align:center;text-transform:uppercase;padding:8px 4px}
.callout-tip{position:absolute;left:258px;top:440px}
</style>
</head>
<body>
<div class="board">

  <!-- Beef burgers -->
  <div class="menu-panel panel-beef"></div>
  <h2 class="section-title title-beef">BEEF BURGERS</h2>
  <div class="note note-beef">All our paties are 100%natural beef. We know because we grind it ourselves. Smashed to order on a hot grill rite in front of you.</div>
  <div class="double-tag" style="left:114px;top:132px;width:126px">DOUBLE PATTY ADD 4</div>

  <div class="item-name" style="left:70px;top:180px">Classic Beef</div>
  <div class="item-price" style="left:282px;top:180px">8.9</div>
  <p class="item-desc" style="left:70px;top:207px">Shredded lettuce, sliced tomato, caramelised onions, beetroot and BBQ sauce on a buttered sesame seed bun</p>

  <div class="item-name" style="left:70px;top:256px">Chesse Burger</div>
  <div class="item-price" style="left:282px;top:256px">9.5</div>
  <p class="item-desc" style="left:70px;top:281px">Dill pickles, minced onion, American cheese, mustard and ketchup on a soft milk bun</p>

  <div class="item-name" style="left:70px;top:326px">Flame Grill</div>
  <div class="item-price" style="left:280px;top:326px">9.5</div>
  <p class="item-desc" style="left:70px;top:352px">Shredded lettuce, sliced tomato, minced onion, dill pickles, American cheese, mayo and ketchup on a soft milk bun</p>

  <div class="item-name" style="left:70px;top:409px">Big Mic</div>
  <div class="item-price" style="left:279px;top:409px">9.9</div>
  <p class="item-desc" style="left:70px;top:436px">Shredded lettuce, dill pickles, minced onion, American cheese and special sauce on a soft milk bun</p>

  <div class="item-name" style="left:70px;top:482px">Truffled</div>
  <div class="item-price" style="left:281px;top:482px">9.9</div>
  <p class="item-desc" style="left:70px;top:509px">Rocket, caramelised onion, dill pickles,havarti cheese and trufle infusedmayo on a soft milk bun</p>

  <!-- Brand -->
  <div class="brand">Rustle<br>Burger</div>
  <div class="tagline">CLASSICS FOR A REASON</div>

  <!-- Chicken burgers -->
  <div class="menu-panel panel-chicken"></div>
  <h2 class="section-title title-chicken">CHICKEN BURGERS</h2>
  <div class="note note-chicken">All our chicken burger patties are prepared onsite daily using premium qulity chicken breast.</div>
  <div class="double-tag" style="left:512px;top:238px;width:128px">DOUBLE PATTY ADD 4</div>

  <div class="item-name" style="left:476px;top:292px">Classic Chicken</div>
  <div class="item-price" style="left:686px;top:292px">8.9</div>
  <p class="item-desc" style="left:476px;top:320px;width:190px">Shredded lettuce, cheese and mayo on a classic sesame seed bun</p>

  <div class="item-name" style="left:476px;top:353px">Pirri Pirri</div>
  <div class="item-price" style="left:686px;top:353px">9.5</div>
  <p class="item-desc" style="left:477px;top:375px;width:170px">Shredded lettuce, cheese, mayo and house made pirri pirri on a classic sesame seed bun</p>

  <div class="item-name" style="left:476px;top:421px">Kentucky</div>
  <div class="item-price" style="left:683px;top:421px">9.9</div>
  <p class="item-desc" style="left:476px;top:448px;width:190px">Shredded lettuce, swiss cheese and feisty mayo on a soft milk bun</p>

  <div class="item-name" style="left:476px;top:485px">El Burger</div>
  <div class="item-price" style="left:683px;top:485px">9.9</div>
  <p class="item-desc" style="left:476px;top:510px;width:200px">Shredded lettuce, salsa, guacamole, cheese and chipotle mayo on a classic sesame seed bun</p>

  <!-- Sides -->
  <h2 class="sides-title">SIDES</h2>
  <section class="sides-panel">
    <div class="row" style="left:32px;top:16px">FRIES</div>
    <div class="row" style="left:230px;top:16px">3.5</div>
    <div class="row" style="left:32px;top:40px">KENTUCKY TENDERS</div>
    <div class="row" style="left:230px;top:40px">6.9</div>
    <p class="small" style="left:32px;top:76px;width:200px">Breaded and fried chicken tenders with secret seasoning. <span class="red">(2 pcs)</span></p>

    <h3 class="sub-title" style="top:132px">NACHOS &amp; LOADED FRIES</h3>
    <div class="choose" style="top:172px">CHOOSE EITHER</div>
    <div class="mid" style="left:58px;top:198px">SEASONED FRIES</div>
    <div class="mid" style="left:212px;top:198px">9.9</div>
    <div class="mid" style="left:58px;top:222px">OR FRESHLY<br>COOKEDCORN CHIPS</div>
    <div class="mid" style="left:210px;top:237px">11.5</div>

    <div class="choose" style="top:270px">CHOOSE ONE</div>
    <p class="small" style="left:62px;top:294px;width:260px;font-size:10px"><span class="red">Gacamole</span> salsa fresca, gacamole, jalapenos, cheese sauce and sour crema</p>
    <p class="small" style="left:62px;top:328px;width:220px;font-size:10px"><span class="red">Beef chilly</span> salsa fresca,beef chilly, jalapenos,cheese sauce andsour crema</p>

    <h3 class="sub-title" style="top:378px">BUFFALO CHICKEN RIBS</h3>
    <div class="mid" style="left:50px;top:424px;line-height:1.08">6 PACK<br>12 PACK<br>24 PACK</div>
    <div class="mid" style="left:134px;top:424px;line-height:1.08">6.9<br>12.9<br>23.9</div>
    <div class="sauce-pill">classic hot sauce<br>or smoky BBQ</div>
    <svg class="callout-tip" width="10" height="14" viewBox="0 0 10 14" aria-hidden="true"><path d="M10 0 L0 7 L10 14 Z" fill="#ffffff"/></svg>
    <div class="callout">Buffalo style fried chicken ribs smotheredin one of our mouth - watering sauces.served with a side of ranch sauce.</div>
  </section>

</div>
</body>
</html>
```